Varnick Fundraising E-mail Campaign

I intend to use Constant Contact to send donors 4 separate e-mail messages with pictures, text and a hot link, “Give to Restore Marlowe.” E-mails will spaced about 3 days apart. I would like the first e-mail to go out on Monday, December 17. The e-mail campaign is part of a board match annual appeal fundraising campaign for a not for profit sleep away Christian camp. Our hope is to raise $40,000.00+

Target Market(s)

Members in Constant Contact list

Colors

Designer to choose colors to be used in the design.

Requirements
Must have
• E- mail recipient must be able to access hot link

```html
<!DOCTYPE html>
<html lang="en">
<head>
<meta charset="utf-8">
<title>Varnick Camp – Revitalize Camp Marlowe Lake</title>
<link href="https://fonts.googleapis.com/css2?family=Roboto+Condensed:wght@400;700&display=swap" rel="stylesheet">
<style>
  :root {
    --page-bg: #adcc88;
    --sheet-bg: #ffffff;
    --banner-red: #e01f2b;
    --camp-green: #0f7a4a;
    --text-green: #12804f;
    --accent-red: #e01f2b;
    --frame-green: #a3c486;
    --photo-dark: #2a2a26;
    --photo-light: #c9c6a0;
    --hill-green: #1f9b48;
    --leaf-green: #8fcf7a;
    --lake-blue: #22b0dc;
  }
  * { box-sizing: border-box; margin: 0; padding: 0; }
  html, body {
    width: 1200px; height: 852px; overflow: hidden;
    background: var(--page-bg);
    font-family: "Roboto Condensed", "Arial Narrow", sans-serif;
  }
  .email {
    position: absolute; left: 376px; top: 0;
    width: 448px; height: 852px;
    background: var(--sheet-bg);
    overflow: hidden;
  }
  .donate-banner {
    height: 24px; background: var(--banner-red);
    text-align: center; line-height: 25px;
  }
  .donate-banner a {
    color: #fff; font-weight: 700; font-size: 15px; text-decoration: underline;
  }
  .brand {
    position: absolute; top: 34px; left: 0; width: 448px;
    display: flex; justify-content: center; align-items: center; gap: 8px;
    color: var(--camp-green);
  }
  .brand-square { width: 30px; height: 30px; background: var(--camp-green); }
  .brand-text { display: flex; flex-direction: column; line-height: 1; }
  .brand-name { font-size: 20px; letter-spacing: 0.5px; }
  .brand-sub { font-size: 6.5px; letter-spacing: 0.4px; margin-top: 2px; text-transform: uppercase; }
  .hero {
    position: absolute; left: 24px; top: 77px; width: 400px; height: 264px;
    border: 3px solid var(--frame-green);
    background: radial-gradient(ellipse at 52% 45%, #5a4a3a 0%, var(--photo-dark) 35%, #3c3a30 60%, var(--photo-light) 100%);
  }
  .copy {
    position: absolute; left: 17px; width: 414px;
    text-align: center; color: var(--text-green);
    font-size: 12.3px; line-height: 16px;
  }
  .copy-intro { top: 365px; }
  .copy-board { top: 461px; }
  .copy-match { top: 524px; color: var(--accent-red); font-weight: 700; font-size: 12.3px; }
  .copy-appeal { top: 572px; }
  .cta {
    position: absolute; top: 651px; left: 20px; width: 408px;
    text-align: center; font-size: 14.5px; line-height: 17px;
  }
  .cta a { color: var(--camp-green); text-decoration: underline; }
  .scene-tree {
    position: absolute; left: 262px; top: 698px; width: 140px; height: 76px;
    background: linear-gradient(180deg, var(--leaf-green), var(--hill-green));
    opacity: 0.85;
  }
  .scene-land {
    position: absolute; left: 0; top: 774px; width: 448px; height: 78px;
    background: linear-gradient(180deg, var(--hill-green) 0%, var(--hill-green) 55%, var(--lake-blue) 100%);
  }
  .contact {
    position: absolute; left: 8px; top: 710px;
    color: var(--camp-green); font-size: 9.6px; line-height: 13.3px;
    font-style: normal;
  }
</style>
</head>
<body>
<main class="email">
  <div class="donate-banner"><a href="#">DONATE NOW</a></div>

  <div class="brand">
    <span class="brand-square"></span>
    <span class="brand-text">
      <span class="brand-name">VARNICK</span>
      <span class="brand-sub">Presbyterian Camp<br>&amp; Conference Center</span>
    </span>
  </div>

  <div class="hero" role="img" aria-label="Photo of a smiling young camper in a cap and sunglasses inside a lakeside lodge"></div>

  <p class="copy copy-intro">Unfortunately, too many of our children spend more time playing video games and watching TV than having fun playing outdoors. Jalen, an average 13-year-old, spends about 300 hours a year playing video games. That's because many parents wonder where they can find a safe and engaging place for their children to experience nature and engaging activities with peers.</p>

  <p class="copy copy-board">The Board of Directors of Varnick Presbyterian Camp and Conference Center decided to create a space that is safe, meaningful and fun by issuing the Revitalize Camp Marlowe Lake Matching Challenge.</p>

  <p class="copy copy-match">They will match on a 1: 1 basis every dollar given or pledged to the campaign by December 31 up to $20,000.00.</p>

  <p class="copy copy-appeal">Please help us create a space where children like Jalen experience nature, connect with other children and have fun!&nbsp; Take advantage of the Revitalize Camp Marlowe Lake Matching Challenge and donate today</p>

  <p class="cta"><a href="#">Visit http://varnickcamp.org/support and click on<br>"Give to Restore Marlowe</a></p>

  <div class="scene-tree" role="img" aria-label="Illustration of a leafy tree on a hillside"></div>
  <div class="scene-land" role="img" aria-label="Illustration of green hills beside a blue lake"></div>

  <address class="contact">
    Contact:<br>
    48 Marlowe Lake Road Varnick, NY 12590<br>
    Phone: 845-555-0142 Fax: 845-555-0178<br>
    E-Mail: office@varnickcamp.org
  </address>
</main>
</body>
</html>
```